Web portal for events

The project is about creating a web application - portal for culture events in Denmark.

Design

We aim for very simplistic, light and fully responsive design. The white background is preferable, as well as light color tones. As inspirational points we like the colors used in www.parvolio.com and www.brindlemoor.org

FORMAT AND REQUIREMENTS:
1. Design should be provided based on the wireframes specified as a link below.
2. The design (and all of its pages) should be provided in three resolution variants:
- Desktop
- Tablet
- Phone
3. The design should be provided as PSD, where each page/section should be in its own PSD file
4. All graphical elements in the design should be delivered as single layers which can then be extracted from the PSD.
5. All graphical elements (icons, graphical buttons, etc.) should be provided as vector objects in the PSD, so that they can be exported into different sizes without loss of quality (for responsiveness)
6. The design should use either web safe fonts or Google Fonts.

RESPONSIVENESS
The web application should be visible on any devices (i.e. responsive design)

WIREFRAMES:
https://velkotrams.examplewire.com/projects/fennoplex/prototype/Homepage?key=3b7c19d0f2a84e6c5d1e9a07b4f2c8d6e1a3f590

We expect design of the following wireframes:

Homepage:
https://velkotrams.examplewire.com/projects/fennoplex/Homepage

For arrangører - billede uploaded:
https://velkotrams.examplewire.com/projects/fennoplex/For%20arrang%C3%B8rer%20-%20billede%20uploaded

Further specifications of the project (i.e. functionality, etc.):
https://files.quorvane.net/document/d/8pKw_Rt2mZqLx4NvB7yHc0aEs9uGdJf3TiOb6nVlW1k/edit?usp=sharing

```html
<!DOCTYPE html>
<html lang="en">
<head>
<meta charset="utf-8">
<title>Kulto – Your Guide To Cultural &amp; Events</title>
<link href="https://fonts.googleapis.com/css2?family=Montserrat:wght@400;500;600;700;800&display=swap" rel="stylesheet">
<style>
:root{
  --red:#e84c4f;
  --dark:#3b3b3b;
  --text:#444;
  --muted:#666;
  --yellow:#f4d73a;
  --sky:#8fd4ee;
  --band:#ececec;
  --line:#dcdcdc;
  --panel:#f0f0f0;
  --white:#fff;
}
*{box-sizing:border-box;margin:0;padding:0}
html,body{width:1108px;height:1200px;overflow:hidden;background:var(--white)}
body{position:relative;font-family:"Montserrat",sans-serif;color:var(--text)}
.abs{position:absolute}
.btn{position:absolute;display:flex;align-items:center;justify-content:center;color:var(--white);font-size:10px;font-weight:500}

/* header */
.brand{left:67px;top:18px;font-size:54px;font-weight:800;color:var(--dark);letter-spacing:-2px;line-height:58px}
.tagline{left:67px;top:78px;font-size:10px;color:var(--text)}
.account{right:68px;top:14px;font-size:11px;font-weight:700;color:var(--dark)}
.search-field{left:284px;top:39px;width:576px;height:25px;border:1px solid #ddd;border-radius:13px;padding-left:12px;font-size:11.5px;display:flex;align-items:center;color:var(--dark)}
.search-btn{left:868px;top:39px;width:66px;height:25px;border-radius:13px;background:var(--dark);font-size:11.5px}
.adv-btn{left:939px;top:39px;width:101px;height:25px;border-radius:13px;background:var(--red);font-size:11.5px}

/* nav */
.nav{left:0;top:101px;width:1108px;height:47px;background:var(--band)}
.nav-item{position:absolute;top:19px;font-size:13px;font-weight:700;color:#555;line-height:13px}
.nav-all{left:67px;top:13px;width:64px;height:22px;border-radius:11px;background:var(--red);color:var(--white);font-size:13px;font-weight:700}

/* content header */
.section-title{font-size:12.5px;font-weight:700;color:var(--dark);top:169px;letter-spacing:.3px}
.sort-label{left:361px;top:169px;font-size:12.5px;font-weight:700;color:var(--dark)}
.order{left:498px;top:164px;width:75px;height:24px;border:1px solid #ccc;font-size:11.5px;color:var(--muted);padding-left:5px;display:flex;align-items:center}
.order span.sep{position:absolute;left:58px;top:4px;width:1px;height:16px;background:#999}
.divider-h{left:0;top:200px;width:1108px;height:1px;background:var(--line)}
.divider-v{left:770px;top:148px;width:1px;height:967px;background:var(--line)}

/* event grid */
.events{left:67px;top:227px;display:grid;grid-template-columns:repeat(3,186px);column-gap:58px;grid-auto-rows:266px}
.card{position:relative}
.card .photo{width:186px;height:108px}
.card h3{margin-top:15px;font-size:11px;font-weight:700;color:#555;letter-spacing:.3px}
.card p{font-size:11.3px;line-height:16px;color:#666;margin-top:2px;letter-spacing:.2px}
.card .date{font-size:9.5px;font-weight:700;color:var(--dark);margin-top:6px}
.card .see{left:0;top:199px;width:67px;height:25px;background:var(--yellow)}
.card .fav{left:75px;top:199px;width:111px;height:25px;background:var(--red)}

/* pagination */
.pager{top:1044px;font-size:10px;color:var(--dark)}
.pg-btn{top:1044px;height:16px;width:36px;background:var(--dark);font-size:10px}

/* sidebar */
.side-photo{left:790px;width:237px;height:130px}
.side-text{left:790px;width:237px;font-size:11.3px;line-height:16px;color:#333}
.side-fav{left:790px;top:852px;width:110px;height:25px;background:var(--sky)}
.newsletter{left:790px;top:904px;width:237px;height:177px;background:var(--panel)}
.newsletter h4{position:absolute;left:44px;top:17px;font-size:15px;font-weight:500;color:#333}
.newsletter .icon{position:absolute;left:15px;top:20px}
.newsletter p{position:absolute;left:15px;top:50px;width:210px;font-size:9.5px;line-height:16px;color:#333}
.newsletter .email{position:absolute;left:15px;top:95px;width:209px;height:34px;background:var(--white);font-size:9.5px;color:#888;display:flex;align-items:center;padding-left:6px}
.newsletter .register{left:17px;top:136px;width:71px;height:25px;background:var(--red)}

/* footer */
.footer-line{left:0;top:1115px;width:1108px;height:1px;background:var(--line)}
.footer-links{left:67px;top:1139px;font-size:9.8px;color:var(--dark);white-space:nowrap;word-spacing:1px}
.footer-links i{font-style:normal;margin:0 8px}
.copyright{left:67px;top:1164px;font-size:9.8px;color:var(--dark)}
.social{left:981px;top:1150px;display:flex;gap:10px}
.social span{width:16px;height:16px;border-radius:50%;background:var(--dark)}
</style>
</head>
<body>

<!-- header -->
<div class="abs brand">KULTO</div>
<div class="abs tagline">Your Guide To cultural &amp; Events</div>
<div class="abs account">LOGIN | SIGN UP</div>
<div class="abs search-field">Search</div>
<div class="btn search-btn">Search</div>
<div class="btn adv-btn">Advance Search</div>

<!-- category nav -->
<nav class="abs nav">
  <div class="btn nav-all">ALL</div>
  <span class="nav-item" style="left:152px">MUSIC</span>
  <span class="nav-item" style="left:234px">SPORTS</span>
  <span class="nav-item" style="left:327px">EXHIBITION</span>
  <span class="nav-item" style="left:436px">OLDER</span>
  <span class="nav-item" style="left:517px">BORN</span>
  <span class="nav-item" style="left:593px">MOTION</span>
  <span class="nav-item" style="left:686px">DIVERSE</span>
</nav>

<!-- list header -->
<div class="abs section-title" style="left:67px">POPULAR EVENTS</div>
<div class="abs sort-label">SORT BY</div>
<div class="btn" style="left:427px;top:164px;width:66px;height:24px;background:var(--dark);font-size:11.5px">Popular</div>
<div class="abs order">Order By<span class="sep"></span>
  <svg style="position:absolute;left:63px;top:9px" width="7" height="5" viewBox="0 0 7 5"><path d="M0.5 0.5 L3.5 4 L6.5 0.5" fill="none" stroke="#333" stroke-width="1.3"/></svg>
</div>
<div class="btn" style="left:601px;top:164px;width:66px;height:24px;background:var(--dark);font-size:11.5px">Date</div>
<div class="btn" style="left:673px;top:164px;width:67px;height:24px;background:var(--red);font-size:11.5px">Price</div>
<div class="abs section-title" style="left:790px">MY FAVOURITE</div>
<div class="abs divider-h"></div>
<div class="abs divider-v"></div>

<!-- events -->
<section class="abs events">
  <article class="card"><div class="photo" role="img" aria-label="Festival crowd with colourful balloons" style="background:linear-gradient(160deg,#eceae4,#d9c6b0 60%,#8a5a3a)"></div>
    <h3>Lorem Ipsum is simply dummy</h3><p>Lorem Ipsum has been the<br>industry's standard</p><div class="date">Posted On : 22.02.2014</div>
    <div class="btn see">See Event</div><div class="btn fav">This Is My Favourite</div></article>
  <article class="card"><div class="photo" role="img" aria-label="Lit event tent on a lawn at dusk" style="background:linear-gradient(180deg,#4e6f9c,#2f4a33 55%,#5d7a3a)"></div>
    <h3>Lorem Ipsum is simply dummy</h3><p>Lorem Ipsum has been the<br>industry's standard</p><div class="date">Posted On : 22.02.2014</div>
    <div class="btn see">See Event</div><div class="btn fav">This Is My Favourite</div></article>
  <article class="card"><div class="photo" role="img" aria-label="Child getting face painting at a fair" style="background:linear-gradient(135deg,#6b3a26,#d8b49a 50%,#c23a2c)"></div>
    <h3>Lorem Ipsum is simply dummy</h3><p>Lorem Ipsum has been the<br>industry's standard</p><div class="date">Posted On : 22.02.2014</div>
    <div class="btn see">See Event</div><div class="btn fav">This Is My Favourite</div></article>

  <article class="card"><div class="photo" role="img" aria-label="Friends chatting at an outdoor market" style="background:linear-gradient(135deg,#d8c7b4,#f2c8cf 55%,#b98d74)"></div>
    <h3>Lorem Ipsum is simply dummy</h3><p>Lorem Ipsum has been the<br>industry's standard</p><div class="date">Posted On : 22.02.2014</div>
    <div class="btn see">See Event</div><div class="btn fav">This Is My Favourite</div></article>
  <article class="card"><div class="photo" role="img" aria-label="White marquee tents on a green field" style="background:linear-gradient(180deg,#4c5a3e,#b9c0bd 50%,#4e7a2e)"></div>
    <h3>Lorem Ipsum is simply dummy</h3><p>Lorem Ipsum has been the<br>industry's standard</p><div class="date">Posted On : 22.02.2014</div>
    <div class="btn see">See Event</div><div class="btn fav">This Is My Favourite</div></article>
  <article class="card"><div class="photo" role="img" aria-label="Night concert crowd under stage lights" style="background:linear-gradient(180deg,#3a1a14,#9c4a2a 45%,#1a1210)"></div>
    <h3>Lorem Ipsum is simply dummy</h3><p>Lorem Ipsum has been the<br>industry's standard</p><div class="date">Posted On : 22.02.2014</div>
    <div class="btn see">See Event</div><div class="btn fav">This Is My Favourite</div></article>

  <article class="card"><div class="photo" role="img" aria-label="Dinner table with glasses under purple light" style="background:linear-gradient(135deg,#6a1c8a,#d04ad0 55%,#f0b7e0)"></div>
    <h3>Lorem Ipsum is simply dummy</h3><p>Lorem Ipsum has been the<br>industry's standard</p><div class="date">Posted On : 22.02.2014</div>
    <div class="btn see">See Event</div><div class="btn fav">This Is My Favourite</div></article>
  <article class="card"><div class="photo" role="img" aria-label="Sports fans cheering in team colours" style="background:linear-gradient(135deg,#2e7a2a,#e7c96a 50%,#c8862e)"></div>
    <h3>Lorem Ipsum is simply dummy</h3><p>Lorem Ipsum has been the<br>industry's standard</p><div class="date">Posted On : 22.02.2014</div>
    <div class="btn see">See Event</div><div class="btn fav">This Is My Favourite</div></article>
  <article class="card"><div class="photo" role="img" aria-label="Audience in a dim hall with warm lights" style="background:linear-gradient(180deg,#4a5a78,#2a2e3c 60%,#15161c)"></div>
    <h3>Lorem Ipsum is simply dummy</h3><p>Lorem Ipsum has been the<br>industry's standard</p><div class="date">Posted On : 22.02.2014</div>
    <div class="btn see">See Event</div><div class="btn fav">This Is My Favourite</div></article>
</section>

<!-- pagination -->
<div class="btn pg-btn" style="left:590px">Pre</div>
<div class="abs pager" style="left:634px">1 &nbsp;| &nbsp;2 &nbsp;| &nbsp;3 &nbsp;........</div>
<div class="btn pg-btn" style="left:704px">Next</div>

<!-- sidebar favourites -->
<div class="abs side-photo" role="img" aria-label="Volunteers greeting each other at an outdoor event" style="top:227px;background:linear-gradient(135deg,#5c7c3c,#e9b9c9 50%,#d8d0c8)"></div>
<p class="abs side-text" style="top:371px">Neque porro quisquam est qui dolorem ipsum quia dolor sit amet, consectetur, adipisci velit...</p>
<div class="abs side-photo" role="img" aria-label="Concert crowd with raised hands under purple lights" style="top:434px;background:radial-gradient(circle at 60% 35%,#f6d4ff,#b02ad8 35%,#3a0c5a 80%)"></div>
<p class="abs side-text" style="top:576px">Neque porro quisquam est qui dolorem ipsum quia dolor sit amet, consectetur, adipisci velit...</p>
<div class="abs side-photo" role="img" aria-label="Beach wedding aisle covered in flower petals" style="top:641px;background:linear-gradient(180deg,#7fb4d8,#e9e2d4 40%,#b3287e 75%,#e8c6d4)"></div>
<p class="abs side-text" style="top:791px">Neque porro quisquam est qui dolorem ipsum quia dolor sit amet, consectetur, adipisci velit...</p>
<div class="btn side-fav">This Is My Favourite</div>

<!-- newsletter -->
<div class="abs newsletter">
  <svg class="icon" width="23" height="15" viewBox="0 0 23 15"><rect x="0.5" y="0.5" width="22" height="14" fill="#555"/><path d="M0.5 0.5 L11.5 8.5 L22.5 0.5 M0.5 14.5 L8.5 7 M22.5 14.5 L14.5 7" fill="none" stroke="#f0f0f0" stroke-width="1"/></svg>
  <h4>Newsletter</h4>
  <p>Lorem Ipsum is simply dummy text of the printing and typesetting industry.</p>
  <div class="email">E-Mail Address</div>
  <div class="btn register">Register</div>
</div>

<!-- footer -->
<div class="abs footer-line"></div>
<div class="abs footer-links">About kulto<i>|</i>Terms &amp; Conditions<i>|</i>Purchase Policy<i>|</i>Newsletter<i>|</i>Contact<i>|</i>Login /Register<i>|</i>Help<i>|</i>For organizers<i>|</i>For Municipalities and tourism</div>
<div class="abs copyright">© 2014 Company Name ,All Rights Reserved</div>
<div class="abs social" aria-label="Social links"><span></span><span></span><span></span></div>

</body>
</html>
```